Home Staging Company needs business card design

We're a home staging company called Brightly Settled Home Staging. We would like a business card design that includes aqua and gray. Our current logo of house within chair is fine but I find we almost always use the logo in one color. I'll upload images of front and back of our current card and our logo. Note that we have dropped "Solutions" from our company name and don't want to include it on the card.

Target Market(s)

Realtors and homeowners - people interested in selling their homes

Contact Information for Business Card

Marisol Thistlewood
Brightly Settled Home Staging
757-555-0193
www.brightlysettled.com
marisol@brightlysettled.com

Font styles to use
Serif
Script

Requirements
Must have
• My logo and contact details
• UPDATE***
• I forgot to say that the company name should be included on the front of the card somehow.

```html
<!DOCTYPE html>
<html lang="en">
<head>
<meta charset="utf-8">
<title>Brightly Settled Home Staging – Business Card</title>
<link rel="stylesheet" href="https://fonts.googleapis.com/css2?family=Playfair+Display:wght@500&family=Roboto+Condensed:wght@400&family=Poppins:wght@300&display=swap">
<style>
  :root {
    --backdrop: #b4b4b4;
    --aqua-top: #5db6bf;
    --aqua-bottom: #1f88b0;
    --aqua: #4fb0b8;
    --paper: #f3f3f3;
    --charcoal: #3a3a3c;
    --ink: #333335;
    --white: #ffffff;
  }
  * { box-sizing: border-box; margin: 0; padding: 0; }
  html, body { width: 1200px; height: 576px; overflow: hidden; }
  body { background: var(--backdrop); position: relative; font-family: "Poppins", sans-serif; }

  .card {
    position: absolute;
    top: 138px;
    width: 484px;
    height: 294px;
    border-radius: 14px;
    overflow: hidden;
  }

  /* Front */
  .card-front {
    left: 82px;
    background: linear-gradient(180deg, var(--aqua-top) 0%, var(--aqua-bottom) 100%);
    color: var(--white);
    text-align: center;
  }
  .front-name {
    position: absolute;
    left: 0; right: 0; top: 112px;
    font-family: "Playfair Display", serif;
    font-weight: 500;
    color: var(--white);
  }
  .front-name .name-main { display: block; font-size: 40px; line-height: 1; }
  .front-name .name-sub { display: block; font-size: 15px; letter-spacing: 8px; margin-top: 12px; }
  .front-web {
    position: absolute;
    left: 0; right: 0; bottom: 16px;
    font-size: 13px;
    font-weight: 300;
  }

  /* Back */
  .card-back { left: 602px; background: var(--paper); }
  .back-shape { position: absolute; inset: 0; }
  .back-brand {
    position: absolute;
    left: 0; width: 196px; top: 70px;
    text-align: center;
    font-family: "Playfair Display", serif;
    font-weight: 500;
    color: var(--ink);
  }
  .brand-dot {
    display: block;
    width: 56px; height: 56px;
    margin: 0 auto 22px;
    border-radius: 50%;
    background: var(--ink);
  }
  .back-brand .name-main { display: block; font-size: 21px; line-height: 1; }
  .back-brand .name-sub { display: block; font-size: 9px; letter-spacing: 4px; margin-top: 6px; }

  .person {
    position: absolute;
    left: 258px; top: 74px;
    color: var(--white);
  }
  .person-name { font-family: "Roboto Condensed", sans-serif; font-size: 20px; font-weight: 400; }
  .person-title { font-size: 11px; font-weight: 300; margin-top: 6px; }

  .contacts {
    position: absolute;
    left: 258px; top: 162px;
    list-style: none;
    color: var(--white);
    font-size: 12px;
    font-weight: 300;
  }
  .contacts li { display: flex; align-items: center; height: 18px; }
  .contacts svg { width: 11px; height: 11px; margin-right: 12px; fill: var(--white); }
</style>
</head>
<body>

<section class="card card-front" aria-label="Card front">
  <h1 class="front-name">
    <span class="name-main">Brightly Settled</span>
    <span class="name-sub">HOME STAGING</span>
  </h1>
  <p class="front-web">www.brightlysettled.com</p>
</section>

<section class="card card-back" aria-label="Card back">
  <svg class="back-shape" viewBox="0 0 484 294" preserveAspectRatio="none" aria-hidden="true">
    <path d="M186 0 C214 90 214 200 188 294 L210 294 C236 200 236 90 194 0 Z" fill="var(--charcoal)"/>
    <path d="M194 0 C236 90 236 200 202 294 L484 294 L484 0 Z" fill="var(--aqua)"/>
  </svg>

  <div class="back-brand">
    <span class="brand-dot"></span>
    <span class="name-main">Brightly Settled</span>
    <span class="name-sub">HOME STAGING</span>
  </div>

  <div class="person">
    <h2 class="person-name">Marisol Thistlewood</h2>
    <p class="person-title">Managing Director</p>
  </div>

  <ul class="contacts">
    <li>
      <svg viewBox="0 0 12 12"><path d="M1 4 C1 2 3 1 6 1 C9 1 11 2 11 4 L9 4.5 L8 3 L4 3 L3 4.5 Z M3 6 L9 6 L10.5 11 L1.5 11 Z"/></svg>
      757-555-0193
    </li>
    <li>
      <svg viewBox="0 0 12 12"><path d="M6 0.5 A5.5 5.5 0 1 0 6 11.5 A5.5 5.5 0 1 0 6 0.5 Z M6 1.8 C7 3 7.5 4.5 7.6 5.4 L4.4 5.4 C4.5 4.5 5 3 6 1.8 Z M4.4 6.6 L7.6 6.6 C7.5 7.5 7 9 6 10.2 C5 9 4.5 7.5 4.4 6.6 Z M1.9 5.4 C2.1 3.8 3.2 2.5 4.6 2 C3.8 3.1 3.3 4.3 3.2 5.4 Z M1.9 6.6 L3.2 6.6 C3.3 7.7 3.8 8.9 4.6 10 C3.2 9.5 2.1 8.2 1.9 6.6 Z M8.8 5.4 C8.7 4.3 8.2 3.1 7.4 2 C8.8 2.5 9.9 3.8 10.1 5.4 Z M8.8 6.6 L10.1 6.6 C9.9 8.2 8.8 9.5 7.4 10 C8.2 8.9 8.7 7.7 8.8 6.6 Z"/></svg>
      www.brightlysettled.com
    </li>
    <li>
      <svg viewBox="0 0 12 12"><path d="M0.5 2 L11.5 2 L6 6.5 Z M0.5 3.2 L6 7.8 L11.5 3.2 L11.5 10 L0.5 10 Z"/></svg>
      marisol@brightlysettled.com
    </li>
  </ul>
</section>

</body>
</html>
```